Veltrano.co - Polar Expeditions Specialists

We need a modern, visually striking business card for Veltrano.co, a company specialized in selling expedition cruises to the most remote regions on Earth, with a focus on the Arctic and Antarctica. The design should instantly communicate that the cardholder is an expert in polar travel. Use clean, premium aesthetics with cool tones like icy blue and white, possibly incorporating polar imagery (ice, glaciers, penguins, etc.)

Attached the logo

Contact Information for Business Card

Feels high-end and trustworthy.. Visually memorable — encourages people to keep it

Colors
0054AA
0677BA
7BADD7
CADEEF
E8F1F8

Requirements
Must have
• ice, glaciers, penguins, montains
Nice to have
• modern, transparente,

```html
<!DOCTYPE html>
<html lang="en">
<head>
<meta charset="utf-8">
<title>Veltrano.co – Business Card</title>
<link href="https://fonts.googleapis.com/css2?family=Poppins:wght@500;700&family=Inter:wght@400;600&display=swap" rel="stylesheet">
<style>
  :root {
    --stage: #787878;
    --navy-deep: #1a2138;
    --navy-mid: #242a42;
    --navy-band: #130f2b;
    --ink: #111111;
    --ice-white: #f4f7fc;
    --muted: #8a8a8a;
    --contact: #555555;
    --card-white: #ffffff;
  }
  * { margin: 0; padding: 0; box-sizing: border-box; }
  html, body { width: 1200px; height: 1200px; overflow: hidden; }
  body { background: var(--stage); position: relative; font-family: "Inter", sans-serif; }

  .card {
    position: absolute;
    left: 179px;
    width: 861px;
    height: 496px;
    box-shadow: 0 10px 24px rgba(0,0,0,0.35);
    overflow: hidden;
  }
  .card--front { top: 84px; }
  .card--back { top: 621px; background: var(--card-white); }

  .front-scene {
    position: absolute; inset: 0;
    background:
      radial-gradient(ellipse at 30% 65%, rgba(60,62,88,0.55), transparent 60%),
      linear-gradient(180deg, var(--navy-mid) 0%, var(--navy-deep) 45%, #1e2236 100%);
  }

  .brand {
    position: absolute;
    display: flex;
    align-items: center;
    gap: 18px;
  }
  .brand__mark {
    width: 62px; height: 62px; border-radius: 50%;
    flex: none;
  }
  .brand__name {
    font-family: "Poppins", sans-serif;
    font-weight: 700;
    font-size: 56px;
    line-height: 1;
    letter-spacing: 0.5px;
  }
  .brand__tagline {
    font-family: "Poppins", sans-serif;
    font-weight: 500;
    font-size: 16.5px;
    margin-top: 8px;
  }
  .brand--light { left: 215px; top: 210px; color: var(--ice-white); }
  .brand--light .brand__mark { background: var(--ice-white); }
  .brand--dark { left: 218px; top: 312px; color: var(--ink); }
  .brand--dark .brand__mark { background: var(--ink); }

  .holder { position: absolute; left: 0; right: 0; text-align: center; }
  .holder__name {
    position: absolute; left: 0; right: 0; top: 214px;
    font-weight: 600; font-size: 29px; letter-spacing: 1px; color: var(--ink);
    text-align: center;
  }
  .holder__role {
    position: absolute; left: 0; right: 0; top: 252px;
    font-size: 24px; letter-spacing: 1px; color: var(--muted);
    text-align: center;
  }

  .contacts {
    position: absolute; top: 338px;
    font-size: 20px; letter-spacing: 2.6px; color: var(--contact);
    line-height: 31px;
  }
  .contacts--left { right: 442px; text-align: right; }
  .contacts--left li { display: flex; justify-content: flex-end; align-items: center; gap: 14px; }
  .contacts--right { left: 445px; }
  .contacts li { list-style: none; }
  .contacts svg { width: 20px; height: 20px; flex: none; }
  .divider {
    position: absolute; left: 429px; top: 337px;
    width: 1.5px; height: 96px; background: var(--ink);
  }
  .base-band {
    position: absolute; left: 0; right: 0; bottom: 0; height: 13px;
    background: var(--navy-band);
  }
</style>
</head>
<body>

<section class="card card--front">
  <div class="front-scene" role="img" aria-label="Dark navy-tinted photo of glaciers, ice cliffs and mountains"></div>
  <div class="brand brand--light">
    <span class="brand__mark"></span>
    <div>
      <div class="brand__name">Veltrano.co</div>
      <div class="brand__tagline">Polar Expeditions Specialists</div>
    </div>
  </div>
</section>

<section class="card card--back">
  <div class="brand brand--dark" style="top:56px;">
    <span class="brand__mark"></span>
    <div>
      <div class="brand__name">Veltrano.co</div>
      <div class="brand__tagline">Polar Expeditions Specialists</div>
    </div>
  </div>

  <div class="holder__name">MARCUS ELLERY</div>
  <div class="holder__role">President/Owner</div>

  <ul class="contacts contacts--left">
    <li>415-555-0142
      <svg viewBox="0 0 24 24" fill="#111"><path d="M6.6 10.8a15.1 15.1 0 0 0 6.6 6.6l2.2-2.2c.3-.3.7-.4 1-.2 1.1.4 2.3.6 3.6.6.6 0 1 .4 1 1V20c0 .6-.4 1-1 1A17 17 0 0 1 3 4c0-.6.4-1 1-1h3.5c.6 0 1 .4 1 1 0 1.3.2 2.5.6 3.6.1.3 0 .7-.2 1z"/></svg>
    </li>
    <li>mail@veltrano.co
      <svg viewBox="0 0 24 24" fill="none" stroke="#111" stroke-width="2"><rect x="2" y="5" width="20" height="14" fill="#111"/><path d="M2 5l10 8 10-8" stroke="#fff" stroke-width="1.5"/></svg>
    </li>
    <li>veltrano.co
      <svg viewBox="0 0 24 24" fill="none" stroke="#111" stroke-width="2"><circle cx="12" cy="12" r="9.5"/><path d="M7 6c2 1 3 3 2 5s1 3 0 5M15 4c-1 2 1 3 3 4M14 20c0-2 2-3 4-3" /></svg>
    </li>
  </ul>

  <div class="divider"></div>

  <ul class="contacts contacts--right">
    <li>48 Harbor Lane</li>
    <li>Port City, ST 20418</li>
    <li>United States</li>
  </ul>

  <div class="base-band"></div>
</section>

</body>
</html>
```